CBD AgriBusiness Verdant Trophy Business Card

We are HiTec producer of medical cannabis CBD Switzerland of high quality. Our website is alpinleaf.net, we will also revisit it graphically, the winner of this contest will be the graphic designer chosen for the new design of the website. We stand out by the skill of the team, many of our engineers we win cup cannabis. I join the current map to take as an example but to revisit completely: deletion of surname and first name, modification of funds (front / back), reorganization of text info, highlighting the address of the website. three characteristics define the business card: Professional, Class, refined. The business card must be optimized for soft-touch and selective varnish printing.

Target Market(s)

Customers and Suppliers

Industry/Entity Type

Agribusiness

Contact Information for Business Card

Logo, Tél / Whatsapp, mail, url du site : alpinleaf.net

Font styles to use
Sans Serif

Requirements
Must have
• Logo of alpinleaf.net
Nice to have
• a design that stands out well on the selective varnish
Should not have
• Last name and first name

```html
<!DOCTYPE html>
<html lang="en">
<head>
<meta charset="utf-8">
<title>alpinleaf business card</title>
<link href="https://fonts.googleapis.com/css2?family=Raleway:wght@700&family=Lato:wght@400&display=swap" rel="stylesheet">
<style>
  :root{
    --backdrop:#ebe8e3;
    --leaf-green:#9dc96f;
    --ink-grey:#56585b;
    --paper:#ffffff;
  }
  *{margin:0;padding:0;box-sizing:border-box}
  html,body{width:1200px;height:900px;overflow:hidden;background:var(--backdrop)}
  .stage{position:relative;width:1200px;height:900px}
  .card{position:absolute;left:330px;width:556px;height:344px;box-shadow:2px 3px 6px rgba(0,0,0,.35)}
  .card--front{top:90px;background:var(--leaf-green)}
  .card--back{top:469px;background:var(--paper)}
  .brand{position:absolute;left:0;right:0;display:flex;align-items:center;justify-content:center;gap:16px}
  .card--front .brand{top:104px}
  .card--back .brand{top:148px}
  .brand__mark{width:40px;height:40px}
  .card--front .brand__mark{background:var(--paper)}
  .card--back .brand__mark{background:var(--leaf-green)}
  .brand__name{font-family:"Raleway",sans-serif;font-weight:700;font-size:58px;line-height:1;color:var(--ink-grey);letter-spacing:.5px}
  .contact-icons{position:absolute;top:198px;left:0;right:0;display:flex;align-items:center;justify-content:center;gap:6px}
  .contact-icons__rule{width:72px;height:1px;background:var(--ink-grey);margin:0 8px}
  .contact-icons svg{display:block;width:28px;height:26px}
  .contact-list{position:absolute;top:238px;left:0;right:0;text-align:center;font-family:"Lato",sans-serif;font-size:18px;line-height:23px;color:var(--ink-grey);list-style:none}
  .card__band{position:absolute;left:0;right:0;bottom:0;height:14px;background:var(--leaf-green)}
</style>
</head>
<body>
<main class="stage">
  <section class="card card--front">
    <div class="brand"><span class="brand__mark"></span><span class="brand__name">alpinleaf</span></div>
    <div class="contact-icons">
      <span class="contact-icons__rule"></span>
      <svg viewBox="0 0 28 26" aria-label="phone"><rect width="28" height="26" rx="2" fill="#56585b"/><path d="M9 6c1 0 2 3 2 4s-1 1-1 2c1 2 3 4 5 5 1 0 1-1 2-1s4 1 4 2-1 3-3 3C12 21 6 15 6 9c0-2 2-3 3-3z" fill="#9dc96f"/></svg>
      <svg viewBox="0 0 28 26" aria-label="email"><rect width="28" height="26" rx="2" fill="#56585b"/><rect x="5" y="7" width="18" height="12" fill="none" stroke="#9dc96f" stroke-width="1.6"/><path d="M5 7l9 7 9-7" fill="none" stroke="#9dc96f" stroke-width="1.6"/></svg>
      <svg viewBox="0 0 28 26" aria-label="website"><rect width="28" height="26" rx="2" fill="#56585b"/><circle cx="14" cy="13" r="8" fill="none" stroke="#9dc96f" stroke-width="1.6"/><path d="M6 13h16M14 5c-4 4-4 12 0 16M14 5c4 4 4 12 0 16" fill="none" stroke="#9dc96f" stroke-width="1.3"/></svg>
      <span class="contact-icons__rule"></span>
    </div>
    <ul class="contact-list">
      <li>+41 79 555 01 42</li>
      <li>office@alpinleaf.net</li>
      <li>www.alpinleaf.net</li>
    </ul>
  </section>
  <section class="card card--back">
    <div class="brand"><span class="brand__mark"></span><span class="brand__name">alpinleaf</span></div>
    <div class="card__band"></div>
  </section>
</main>
</body>
</html>
```